Website for my photography business

I need a website for my photography business, Bram Kellet Photography. I need a website that has a landing page with a cover photo of each kind of photography I do. For example, Nature, Weddings, Portraits and Architecture. I want it so that when someone comes onto my website they have to choose which kind of photography page they want to visit. So if they click on the wedding photo it will open to a page with my wedding portfolio images and a contact me button. If they choose nature photography I want them to be redirected to an e-commerce section where they can purchase prints. Architecture and Portraits should open up to their respective portfolios with about me and contact info. I like this kind of format because I want people who come to my website for a specific type of photography to be able to be directed there easily without having to look at a mix of other kinds of photography. I will provide a few files to use as placeholders. I have already purchased the bramkelletphotography.example domain name. A Wix website would be great because I am most familiar with it but I am open to anything.

Industry/Entity Type

Photographer

Number of Pages Required

5+ page

Requirements
Must have
• Landing Page and e-commerce

```html
<!DOCTYPE html>
<html lang="en">
<head>
<meta charset="utf-8">
<title>Bram Kellet Photography – Portraits</title>
<link rel="stylesheet" href="https://fonts.googleapis.com/css2?family=Poppins:wght@400;500;600;700&family=Allura&display=swap">
<style>
:root{
  --purple:#3d386c;
  --purple-deep:#3a3464;
  --purple-box:#4a3f80;
  --teal:#1e5470;
  --ink:#222;
  --paper:#ffffff;
  --mist:#f4f4f4;
  --grey-box:#c9c9c9;
}
*{box-sizing:border-box;margin:0;padding:0}
html,body{width:1200px;height:3210px;overflow:hidden}
body{font-family:"Poppins",sans-serif;color:var(--ink);background:var(--paper);position:relative}
.abs{position:absolute}
.script{font-family:"Allura",cursive;font-weight:400}

.topbar{left:0;top:0;width:1200px;height:31px;border-bottom:1px solid #e2e2e2;text-align:center;font-size:12px;line-height:31px;color:#555}
.header{left:0;top:31px;width:1200px;height:101px}
.brand{left:112px;top:30px;display:flex;align-items:center;gap:10px;font-size:21px;font-weight:500;color:var(--purple)}
.brand-dot{width:14px;height:14px;border:2px solid var(--purple);border-radius:50%}
.socials{left:669px;top:33px;display:flex;gap:5px}
.soc{width:36px;height:36px;border:1.5px solid #222;border-radius:50%;display:flex;align-items:center;justify-content:center}
.call{left:871px;top:31px;width:217px;height:43px;border-radius:22px;background:var(--teal);color:#fff;font-weight:600;font-size:17px;line-height:43px;text-align:center}

.nav{left:0;top:132px;width:1200px;height:39px;background:var(--purple);display:flex;justify-content:center}
.nav a{color:#fff;text-decoration:none;font-size:15px;font-weight:500;line-height:39px;padding:0 17px}
.nav a.active{background:var(--teal)}

.hero{left:0;top:171px;width:1200px;height:400px;
  background:
    radial-gradient(ellipse 380px 260px at 22% 30%,rgba(230,230,230,.85),transparent 70%),
    radial-gradient(ellipse 300px 420px at 78% 25%,rgba(210,210,210,.8),transparent 70%),
    radial-gradient(ellipse 500px 180px at 55% 95%,rgba(180,180,180,.7),transparent 70%),
    linear-gradient(100deg,#3a3a3a 0%,#8d8d8d 30%,#5a5a5a 55%,#9a9a9a 75%,#111 100%)}
.hero-box{left:345px;top:254px;width:510px;height:233px;background:rgba(74,66,110,.86);text-align:center;color:#fff}
.hero-box h1{font-size:50px;margin-top:12px;line-height:56px;font-weight:700}
.hero-box p{font-size:17px;font-weight:500;line-height:27px;margin-top:10px}
.btn{display:inline-block;background:var(--teal);color:#fff;font-weight:600;font-size:17px;border-radius:24px;text-decoration:none}
.hero-box .btn{margin-top:18px;width:177px;height:47px;line-height:47px}

.section-title{left:0;width:1200px;text-align:center;font-size:48px;color:var(--purple)}

.grid{left:128px;top:733px;width:944px;display:flex;gap:21px;align-items:flex-start}
.col{width:300px;display:flex;flex-direction:column;gap:23px}
.card{background:#fff;box-shadow:0 1px 6px rgba(0,0,0,.14)}
.photo{width:100%;position:relative;overflow:hidden}
.photo::after{content:"";position:absolute;inset:0;background:radial-gradient(ellipse at 50% 45%,transparent 55%,rgba(0,0,0,.22) 100%)}
.card p{height:51px;line-height:51px;text-align:center;font-size:17px;color:#222}

.about-photo{left:0;top:1956px;width:634px;height:396px;
  background:
    radial-gradient(ellipse 200px 260px at 25% 60%,rgba(80,90,100,.75),transparent 70%),
    radial-gradient(ellipse 260px 200px at 75% 70%,rgba(150,200,90,.8),transparent 70%),
    radial-gradient(ellipse 200px 300px at 60% 20%,rgba(230,240,200,.7),transparent 70%),
    linear-gradient(110deg,#4b5a3c 0%,#7e8f5c 45%,#b9cc8e 70%,#5c6c44 100%)}
.about{left:634px;top:1956px;width:566px;height:396px;background:var(--teal)}
.about h2{position:absolute;left:36px;top:44px;font-size:48px;color:#fff;line-height:56px}
.about p{position:absolute;left:36px;top:124px;width:418px;font-size:14.5px;line-height:27.4px;color:#fff;text-align:justify}

.touch{left:0;top:2352px;width:1200px;height:500px;background:var(--mist)}
.tiles{left:224px;top:2539px;display:flex;gap:5px}
.tile{width:247px;height:203px;text-align:center;color:#fff;font-size:16px;line-height:24px;padding-top:48px}
.tile svg{display:block;margin:0 auto 12px}
.tile.mail{background:var(--teal)}
.tile.phone{background:var(--grey-box);color:#333}
.tile.place{background:var(--purple-box)}

.footer{left:0;top:2852px;width:1200px;height:358px;background:var(--purple-deep);color:#fff}
.fcol{position:absolute;top:56px}
.fcol h3{font-size:16px;font-weight:600;margin-bottom:18px}
.fcol ul{list-style:none;font-size:13px;line-height:26.5px}
.contact li{display:flex;align-items:flex-start;gap:10px;line-height:29px}
.contact svg{margin-top:9px;flex:none}
.contact .addr{line-height:14px;padding-top:6px}
.contact u{text-underline-offset:3px}
.news-input{position:absolute;left:821px;top:2957px;width:267px;height:35px;border-radius:18px;background:#fff;color:#666;font-size:13px;line-height:35px;padding-left:17px}
.submit{position:absolute;left:821px;top:3007px;width:155px;height:35px;border-radius:18px;background:var(--teal);color:#fff;font-weight:600;font-size:15px;line-height:35px;text-align:center}
.fsoc{left:841px;top:3068px;display:flex;gap:7px}
.fsoc span{width:36px;height:36px;border-radius:50%;background:#fff;display:flex;align-items:center;justify-content:center}
.copy{left:0;top:3162px;width:1200px;text-align:center;font-size:13px;color:#fff}
</style>
</head>
<body>

<div class="abs topbar">Lorem ipsum dolor sit amet, consectetur adipiscing elit,</div>

<header class="abs header">
  <div class="abs brand"><span class="brand-dot"></span>Bram Kellet Photography</div>
  <div class="abs socials">
    <span class="soc" aria-label="Website"><svg width="16" height="16" viewBox="0 0 16 16" fill="none" stroke="#222" stroke-width="1.4"><circle cx="8" cy="8" r="6.5"/><path d="M1.5 8h13M8 1.5c2.2 2 2.2 11 0 13M8 1.5c-2.2 2-2.2 11 0 13"/></svg></span>
    <span class="soc" aria-label="Share link"><svg width="16" height="16" viewBox="0 0 16 16" fill="none" stroke="#222" stroke-width="1.5" stroke-linecap="round"><path d="M7 9.5a3 3 0 0 0 4.2 0l2.3-2.3a3 3 0 0 0-4.2-4.2L8.4 3.9"/><path d="M9 6.5a3 3 0 0 0-4.2 0L2.5 8.8a3 3 0 0 0 4.2 4.2l.9-.9"/></svg></span>
    <span class="soc" aria-label="Message"><svg width="16" height="16" viewBox="0 0 16 16" fill="none" stroke="#222" stroke-width="1.4" stroke-linejoin="round"><path d="M2 3h12v8H7l-3 3v-3H2z"/></svg></span>
    <span class="soc" aria-label="Email"><svg width="16" height="16" viewBox="0 0 16 16" fill="none" stroke="#222" stroke-width="1.4"><rect x="1.5" y="3.5" width="13" height="9" rx="1"/><path d="M2 4l6 5 6-5"/></svg></span>
  </div>
  <div class="abs call">Call Us: 555-010-2040</div>
</header>

<nav class="abs nav">
  <a href="#">Home</a><a href="#">About Me</a><a href="#">Nature</a><a href="#">Weddings</a><a class="active" href="#">Potraits</a><a href="#">Architecture</a><a href="#">Shop</a><a href="#">portfolio</a><a href="#">News</a><a href="#">Contact Us</a>
</nav>

<section class="abs hero" role="img" aria-label="Black and white close-up portrait photograph"></section>
<div class="abs hero-box">
  <h1 class="script">Portraits</h1>
  <p>Lorem ipsum dolor sit amet, consectetur adipiscing<br>elit, sed do eiusmod tempor incididunt</p>
  <a class="btn" href="#">CONTACT ME</a>
</div>

<h2 class="abs section-title script" style="top:645px">Portraits Portfolio</h2>

<div class="abs grid">
  <div class="col">
    <div class="card"><div class="photo" role="img" aria-label="Smiling woman in sunglasses picking apples" style="height:299px;background:radial-gradient(ellipse 120px 90px at 70% 40%,#3a2a24,transparent 70%),radial-gradient(ellipse 140px 80px at 70% 88%,#d79a98,transparent 70%),radial-gradient(ellipse 120px 140px at 20% 30%,#9cc25a,transparent 70%),linear-gradient(135deg,#4f7a2a,#88a84e 50%,#b98a80)"></div><p>Lorem ipsum dolor sit amet</p></div>
    <div class="card"><div class="photo" role="img" aria-label="Blonde woman posing in soft sunlight" style="height:306px;background:radial-gradient(ellipse 110px 150px at 52% 38%,#e9cf9e,transparent 70%),radial-gradient(ellipse 150px 80px at 55% 92%,#f3ede0,transparent 70%),radial-gradient(ellipse 100px 180px at 10% 50%,#b99a6a,transparent 70%),linear-gradient(135deg,#cdb58a,#efe2c8 55%,#a8926a)"></div><p style="height:41px;line-height:30px">Lorem ipsum dolor sit amet</p></div>
    <div class="card"><div class="photo" role="img" aria-label="Family with child on shoulders in a meadow" style="height:323px;background:radial-gradient(ellipse 60px 120px at 42% 62%,#6a6a5a,transparent 70%),radial-gradient(ellipse 50px 100px at 70% 70%,#f0ece0,transparent 70%),linear-gradient(180deg,#3e8ad8 0%,#8cc0ea 45%,#cfe4f2 62%,#9aae52 72%,#6e8a34 100%)"></div><p style="height:55px;line-height:55px">Lorem ipsum dolor sit amet</p></div>
  </div>
  <div class="col">
    <div class="card"><div class="photo" role="img" aria-label="Man in denim jacket on a hillside" style="height:216px;background:radial-gradient(ellipse 90px 70px at 50% 85%,#34557e,transparent 70%),radial-gradient(ellipse 60px 60px at 48% 35%,#b58a70,transparent 70%),linear-gradient(180deg,#c2d8e6 0%,#a8c4d2 30%,#7d9a5a 45%,#4d6a34 100%)"></div><p>Lorem ipsum dolor sit amet</p></div>
    <div class="card"><div class="photo" role="img" aria-label="Woman in patterned top at golden hour" style="height:325px;background:radial-gradient(ellipse 90px 120px at 48% 35%,#c07a48,transparent 70%),radial-gradient(ellipse 140px 90px at 40% 85%,#d0522a,transparent 70%),radial-gradient(ellipse 120px 160px at 15% 30%,#2f4a22,transparent 70%),linear-gradient(135deg,#3f5a2a,#8a7a3a 50%,#e0a040)"></div><p style="height:54px;line-height:54px">Lorem ipsum dolor sit amet</p></div>
    <div class="card"><div class="photo" role="img" aria-label="Woman with notebook by the water" style="height:303px;background:radial-gradient(ellipse 80px 110px at 62% 40%,#b0784e,transparent 70%),radial-gradient(ellipse 120px 90px at 60% 80%,#6a5a3a,transparent 70%),linear-gradient(180deg,#1c2f52,#2f4a74 60%,#3c5680)"></div><p style="height:43px;line-height:43px">Lorem ipsum dolor sit amet</p></div>
  </div>
  <div class="col">
    <div class="card"><div class="photo" role="img" aria-label="Woman running through autumn forest" style="height:381px;background:radial-gradient(ellipse 80px 110px at 55% 30%,#1f8ea0,transparent 70%),radial-gradient(ellipse 70px 120px at 12% 40%,#6a5236,transparent 70%),radial-gradient(ellipse 160px 80px at 50% 92%,#8a4a20,transparent 70%),linear-gradient(180deg,#e6d0a0,#c08a4a 55%,#7a4a2a)"></div><p>Lorem ipsum dolor sit amet</p></div>
    <div class="card"><div class="photo" role="img" aria-label="Dark-haired woman against green foliage" style="height:217px;background:radial-gradient(ellipse 80px 100px at 48% 40%,#2a1e1a,transparent 70%),radial-gradient(ellipse 70px 60px at 50% 85%,#d9a890,transparent 70%),linear-gradient(135deg,#2e5a1e,#7aa84a 55%,#3e6a24)"></div><p style="height:49px;line-height:49px">Lorem ipsum dolor sit amet</p></div>
    <div class="card"><div class="photo" role="img" aria-label="Smiling cyclist in helmet leaning on bike" style="height:325px;background:radial-gradient(ellipse 70px 50px at 50% 15%,#c8c8c8,transparent 70%),radial-gradient(ellipse 140px 110px at 45% 60%,#3a78aa,transparent 70%),radial-gradient(ellipse 150px 70px at 50% 95%,#2a2a2a,transparent 70%),linear-gradient(135deg,#9a6438,#6a5a4a 50%,#b0683a)"></div><p style="height:55px;line-height:55px">Lorem ipsum dolor sit amet</p></div>
  </div>
</div>

<div class="abs about-photo" role="img" aria-label="Photographer shooting with a telephoto lens in a forest"></div>
<section class="abs about">
  <h2 class="script">About Me</h2>
  <p>Lorem ipsum dolor sit amet, consectetur adipiscing elit, sed do eiusmod tempor incididunt ut labore et dolore magna aliqua. Ut enim ad minim veniam, quis nostrud exercitation ullamco laboris nisi ut aliquip ex commodo consequat. Duis aute irure dolor reprehenderit voluptate velit esse cillum dolore eu fugiat nulla pariatur. Excepteur sint occaecat cupidatat non proident, sunt in culpa qui officia deserunt mollit anim id est laborum.</p>
</section>

<section class="abs touch"></section>
<h2 class="abs section-title script" style="top:2450px">Get In Touch</h2>
<div class="abs tiles">
  <div class="tile mail">
    <svg width="44" height="44" viewBox="0 0 44 44" fill="none" stroke="#fff" stroke-width="2" stroke-linejoin="round"><path d="M40 4 4 20l14 5 4 14 6-10 12-25z"/><path d="M40 4 18 25"/></svg>
    info@bramkelletphoto<br>graphy.example
  </div>
  <div class="tile phone">
    <svg width="44" height="44" viewBox="0 0 44 44" fill="none" stroke="#333" stroke-width="2" stroke-linejoin="round"><path d="M10 6l7 8-4 5c3 6 7 10 13 13l5-4 8 7-4 5C22 40 4 22 6 10z"/><path d="M26 6a12 12 0 0 1 12 12M26 12a6 6 0 0 1 6 6"/></svg>
    555 014 2288<br>555 019 7731
  </div>
  <div class="tile place">
    <svg width="44" height="44" viewBox="0 0 44 44" fill="none" stroke="#fff" stroke-width="2"><path d="M22 40S10 27 10 17a12 12 0 0 1 24 0c0 10-12 23-12 23z"/><circle cx="22" cy="17" r="5"/></svg>
    #2868 Lorem ipsum dolor<br>sit amet, consectetur
  </div>
</div>

<footer class="abs footer">
  <div class="fcol" style="left:112px">
    <h3>CONTACT INFO</h3>
    <ul class="contact">
      <li><svg width="13" height="11" viewBox="0 0 13 11" fill="#fff"><path d="M1 3c3-3 8-3 11 0v2H9V3.5H4V5H1z"/><rect x="2" y="6" width="9" height="5" rx="1"/></svg>(555) 014-2288</li>
      <li><svg width="13" height="11" viewBox="0 0 13 11" fill="#fff"><rect x="3" y="0" width="7" height="3"/><rect x="0" y="4" width="13" height="5" rx="1"/><rect x="3" y="7" width="7" height="4"/></svg>(555) 014-2289</li>
      <li><svg width="13" height="10" viewBox="0 0 13 10" fill="#fff"><rect width="13" height="10" rx="1"/><path d="M1 1l5.5 5L12 1" stroke="#3a3464" fill="none"/></svg><u>hello@kelletstudio.example</u></li>
      <li><svg width="11" height="14" viewBox="0 0 11 14" fill="#fff"><path d="M5.5 14S0 8 0 5.5a5.5 5.5 0 0 1 11 0C11 8 5.5 14 5.5 14zM5.5 3.5a2 2 0 1 0 0 4 2 2 0 0 0 0-4z"/></svg><span class="addr">#2868 Lorem ipsum dolor<br>sit amet, consectetur</span></li>
    </ul>
  </div>
  <div class="fcol" style="left:373px">
    <h3>QUICK LINKS</h3>
    <ul><li>Home</li><li>About</li><li>Professional Gamer</li><li>Reviews</li><li>Gallery</li></ul>
  </div>
  <div class="fcol" style="left:601px">
    <h3>INFORMATION</h3>
    <ul><li>Terms &amp; Conditions</li><li>Privacy Policy</li><li>Disclaimer</li><li>Site Map</li><li>Contact Us</li></ul>
  </div>
  <div class="fcol" style="left:820px;top:58px">
    <h3>NEWSLETTER SUBSCRIPTION</h3>
  </div>
</footer>
<div class="news-input">Enter your email</div>
<div class="submit">SUBMIT</div>
<div class="abs fsoc">
  <span aria-label="Website"><svg width="16" height="16" viewBox="0 0 16 16" fill="none" stroke="#3a3464" stroke-width="1.5"><circle cx="8" cy="8" r="6.5"/><path d="M1.5 8h13M8 1.5c2.2 2 2.2 11 0 13M8 1.5c-2.2 2-2.2 11 0 13"/></svg></span>
  <span aria-label="Share link"><svg width="16" height="16" viewBox="0 0 16 16" fill="none" stroke="#3a3464" stroke-width="1.6" stroke-linecap="round"><path d="M7 9.5a3 3 0 0 0 4.2 0l2.3-2.3a3 3 0 0 0-4.2-4.2L8.4 3.9"/><path d="M9 6.5a3 3 0 0 0-4.2 0L2.5 8.8a3 3 0 0 0 4.2 4.2l.9-.9"/></svg></span>
  <span aria-label="Message"><svg width="16" height="16" viewBox="0 0 16 16" fill="none" stroke="#3a3464" stroke-width="1.5" stroke-linejoin="round"><path d="M2 3h12v8H7l-3 3v-3H2z"/></svg></span>
  <span aria-label="Email"><svg width="16" height="16" viewBox="0 0 16 16" fill="none" stroke="#3a3464" stroke-width="1.5"><rect x="1.5" y="3.5" width="13" height="9" rx="1"/><path d="M2 4l6 5 6-5"/></svg></span>
</div>
<div class="abs copy">© Copyright 2020 Bram Kellet Photography, All Rights Reserved</div>

</body>
</html>
```